Sablecrest Care Allies Business Flyers

I am in need of a nice, professional brochure that I can leave behind with my clients. I have template built, but will need a new design that I can be proud of and that I can have the template to update and change down the road. I will want to reflect my medical distribution services in the form of Labs I partner with (Genetic Testing and Pathology) and Pharmacies I partner with for Topical solutions (creams for commercial and medicare) as well as worker's compensation. Finally, I have toxicology testing.

Target Market(s)

Medical clinics, physicians

Industry/Entity Type

Medical

Font styles to use
Other font styles liked:
• see brochure (Avenir Next) NOTE: Feel free to use another font if you think it is more elegant and/or a better option

Colors
000000
cbcbcb
f7f7f7

Requirements
Must have
• Focus on my brand (trusted partner) showcase the logo (carbon fiber look on all black areas) See the bottom right of the brochure I uploaded. On the inside, I want to feature my labs and pharmacy(s). I will send you the link to them so you can use items from their websites. We are focusing on PROFESSIONAL and TRUSTED service with strong partnerships with world class labs, etc.
• Focus on we handle all the billing and collection processes. All of our partners are chosen because they have your patient satisfaction in mind as a top priority. We are always on the "right side" of insurance and are HIPPA compliant and have a zero tolerance for non-compliance.
• What we do: Testing (Toxicology and Genetic Testing) Pharmacogenetics studies how genetic various impact the way our bodies respond to certain medications. By having detailed patient data, physicians can now practice precise, individualized, tailored treatment programs based on personal date of each patient.
Nice to have
• Note the importance of the "mirroring/reflection" in my logo on the "P" and the "carbon fiber" look and feel on the black "M". if you can build that into the look and feel of the brochure, it would help to "pop" the brand and my logo.
• Build the partner labs/pharmacy into the brochure for credibility. ( I would say some of our key partners and leave it opened ended like we have many more)
• Topical Solutions: www.brinvalewellco.com (innovation/innovative medicare and commercial insurance solutions
• www.tarqinmedix.com (workers comp solutions)
• Labs:
• www.quorvendiagnostic.com
• www.pelmorabio.com
• I will provide more content and verbiage if needed, but much of it you can get from the website. The key is that we do all the billing, we supply all the materials including paperwork, forms, collection kits and all shipping. We differentiate ourselves by taking all the cumbersome work away from the staff through automation and best practices, topped off by personal/customized service.
Should not have
• Cluttered and busy...not many colors that create confusion and/or attention span issues.

```html
<!DOCTYPE html>
<html lang="en">
<head>
<meta charset="utf-8">
<title>Sablecrest Care Allies – Inside Spread</title>
<link rel="stylesheet" href="https://fonts.googleapis.com/css2?family=Nunito+Sans:wght@400;600;700;800&display=swap">
<style>
:root{
  --stage:#a5a6aa;
  --ink:#000000;
  --text:#1c1c1c;
  --mist:#cbcbcb;
  --paper:#f7f7f7;
  --panel-light:#eeeeee;
  --white:#ffffff;
  --carbon-a:#040404;
  --carbon-b:#141414;
  --muted:#5a5a5a;
}
*{box-sizing:border-box;margin:0;padding:0}
html,body{width:1200px;height:931px;overflow:hidden;background:var(--stage)}
body{font-family:"Nunito Sans",Arial,sans-serif;color:var(--text);position:relative}
.spread{position:absolute;left:51px;top:38px;width:1105px;height:854px;background:var(--white)}
.panel{position:absolute;top:0;height:854px;overflow:hidden}
.panel--services{left:0;width:369px;background:var(--panel-light)}
.panel--testimonials{left:369px;width:368px;background:linear-gradient(180deg,var(--carbon-b),var(--carbon-a) 40%,var(--carbon-b) 100%)}
.panel--partners{left:737px;width:368px;background:var(--white)}
.base-band{position:absolute;left:0;right:0;bottom:0;height:22px;background:linear-gradient(180deg,#2a2a2a,#0a0a0a)}
.photo{position:absolute;display:block}
.photo--lab{left:0;top:0;width:369px;height:225px;background:linear-gradient(135deg,#c9d2dc,#8a99aa 55%,#dfe4ea)}
.photo--handshake{left:0;top:0;width:368px;height:225px;background:linear-gradient(135deg,#6b7480,#c4ccd6 50%,#e9edf2)}
.photo--inset{border:4px solid var(--white)}
.photo--inset-a{left:50px;top:150px;width:98px;height:96px;transform:rotate(-12deg);background:linear-gradient(135deg,#e8e8e8,#9aa4ad)}
.photo--inset-b{left:153px;top:152px;width:100px;height:92px;transform:rotate(10deg);background:linear-gradient(135deg,#d8e6ea,#b77f6a)}
.photo--inset-c{left:240px;top:160px;width:100px;height:90px;transform:rotate(4deg);background:linear-gradient(135deg,#bfc8cf,#e8ecef)}
.section-title{position:absolute;font-weight:600;font-size:22px;letter-spacing:.2px;color:var(--ink);text-transform:uppercase;line-height:26px}
.service{position:absolute;left:27px;width:330px;height:110px}
.service__icon{position:absolute;left:0;top:0;width:60px;height:60px;border-radius:50%}
.service__name{position:absolute;left:78px;top:0;font-weight:700;font-size:17px;color:var(--ink);text-transform:uppercase;line-height:20px}
.service__body{position:absolute;left:78px;top:19px;width:232px;font-size:13px;line-height:16.7px}
.icon--testing{background:linear-gradient(135deg,#cfe3f3,#6e9cc6 60%,#e07a3a)}
.icon--topicals{background:radial-gradient(circle at 35% 45%,#f3efe8 20%,#b16d55 45%,#5a3026)}
.icon--toxicology{background:linear-gradient(135deg,#3d7fc4,#c8242c 60%,#9fc4e6)}
.quote{position:absolute;left:0;width:368px;color:var(--white)}
.quote__mark{position:absolute;left:28px;top:-4px;font-size:30px;font-weight:800;line-height:30px}
.quote__mark--close{position:absolute;font-size:30px;font-weight:800;line-height:30px}
.quote__text{position:absolute;left:55px;top:0;width:280px;font-size:13px;line-height:16.7px}
.quote__author{position:absolute;left:55px;font-weight:800;font-size:15px;font-style:normal}
.partner-group{position:absolute;width:330px}
.partner-group__name{position:absolute;left:0;top:0;font-weight:700;font-size:16px;color:var(--ink)}
.partner-group__body{position:absolute;left:0;top:22px;width:295px;font-size:13px;line-height:16.7px}
.partner-mark{position:absolute;display:flex;align-items:center;gap:5px;font-weight:700;font-size:12px;color:var(--muted);white-space:nowrap}
.partner-mark__dot{width:14px;height:14px;background:var(--muted);border-radius:50%}
.partner-mark__square{width:14px;height:14px;background:var(--muted)}
.partner-mark--box{height:32px;padding:0 12px;background:#6d6d6d;color:var(--white);font-size:13px;letter-spacing:1.5px}
.reference{position:absolute;left:23px;width:340px;height:110px}
.reference__photo{position:absolute;left:0;top:-4px;width:60px;height:60px;border-radius:50%}
.reference__text{position:absolute;left:76px;top:0;width:232px;font-size:13px;line-height:16.7px}
.ref--bottles{background:radial-gradient(circle at 40% 50%,#e7a34c,#c9d3dc 60%,#eef1f4)}
.ref--vial{background:radial-gradient(circle at 45% 55%,#9ac1e0,#e2e6ea 55%,#cfd6dc)}
</style>
</head>
<body>
<main class="spread">

  <section class="panel panel--services">
    <div class="photo photo--lab" role="img" aria-label="Laboratory scientist working with samples at a lab bench"></div>
    <div class="photo photo--inset photo--inset-a" role="img" aria-label="Stethoscope on a desk"></div>
    <div class="photo photo--inset photo--inset-b" role="img" aria-label="Pharmacy shelves stocked with medicines"></div>
    <h2 class="section-title" style="left:31px;top:270px">What we do:</h2>

    <article class="service" style="top:318px">
      <div class="service__icon icon--testing" role="img" aria-label="Pipette dropping samples into a test tray"></div>
      <h3 class="service__name">Testing</h3>
      <p class="service__body">Lorem ipsum dolor sit amet, ligula suspendisse nulla pretium, rhoncus tempor fermentum, enim integer ad vestibulum volutpat. Nisl rhoncus turpis est, vel elit, congue wisi enim nunc ultricies sit, magna tincidunt.</p>
    </article>
    <article class="service" style="top:491px">
      <div class="service__icon icon--topicals" role="img" aria-label="Topical cream on a fingertip"></div>
      <h3 class="service__name">Topicals</h3>
      <p class="service__body">Lorem ipsum dolor sit amet, ligula suspendisse nulla pretium, rhoncus tempor fermentum, enim integer ad vestibulum volutpat. Nisl rhoncus turpis est, vel elit, congue wisi enim nunc ultricies sit, magna tincidunt.</p>
    </article>
    <article class="service" style="top:664px">
      <div class="service__icon icon--toxicology" role="img" aria-label="Test tubes with red samples"></div>
      <h3 class="service__name">Toxicology</h3>
      <p class="service__body">Lorem ipsum dolor sit amet, ligula suspendisse nulla pretium, rhoncus tempor fermentum, enim integer ad vestibulum volutpat. Nisl rhoncus turpis est, vel elit, congue wisi enim nunc ultricies sit, magna tincidunt.</p>
    </article>
    <div class="base-band"></div>
  </section>

  <section class="panel panel--testimonials">
    <blockquote class="quote" style="top:39px">
      <span class="quote__mark">“</span>
      <p class="quote__text">Consectetuer arcu ipsum ornare pellen-tesque vehicula, in vehicula diam, ornare magna rat felis wisi a risus. Justo fermentum id. Malesuada eleifend, tortor molestie, a a vel et. Mauris at suspendisse, neque aliquam faucibus adipiscing, vivamus in. Wisi mattis leo suscipit nec amet, nisl fermentum tempor ac a, augue psum ornare pellentesque vehicula, in vehicula diam ipsum ornare pellentesque vehicula.</p>
      <span class="quote__mark--close" style="left:290px;top:155px">”</span>
      <cite class="quote__author" style="top:182px">Lorem ipsum dolor</cite>
    </blockquote>
    <blockquote class="quote" style="top:276px">
      <span class="quote__mark">“</span>
      <p class="quote__text">Consectetuer arcu ipsum ornare pellen-tesque vehicula, in vehicula diam, ornare magna rat felis wisi a risus. Justo fermentum id. Malesuada eleifend, tortor molestie, a a vel et. Mauris at suspendisse, neque aliquam faucibus adipiscing.</p>
      <span class="quote__mark--close" style="left:290px;top:88px">”</span>
      <cite class="quote__author" style="top:116px">Lorem ipsum dolor</cite>
    </blockquote>
    <blockquote class="quote" style="top:446px">
      <span class="quote__mark">“</span>
      <p class="quote__text">Consectetuer arcu ipsum ornare pellen-tesque vehicula, in vehicula diam, ornare magna rat felis wisi a risus. Justo fermentum id. Malesuada eleifend, tortor molestie, a a vel et. Mauris at suspendisse, neque aliquam faucibus adipiscing, vivamus in. Wisi mattis leo suscipit nec amet, nisl fermentum tempor ac a, augue psum ornare pellentesque vehicula, in vehicula diam ipsum ornare pellentesque vehicula.</p>
      <span class="quote__mark--close" style="left:290px;top:155px">”</span>
      <cite class="quote__author" style="top:182px">Lorem ipsum dolor</cite>
    </blockquote>
    <blockquote class="quote" style="top:682px">
      <span class="quote__mark">“</span>
      <p class="quote__text">Consectetuer arcu ipsum ornare pellen-tesque vehicula, in vehicula diam, ornare magna rat felis wisi a risus. Justo fermentum id. Malesuada eleifend, tortor molestie, a a vel et. Mauris at suspendisse, neque aliquam faucibus adipiscing.</p>
      <span class="quote__mark--close" style="left:290px;top:88px">”</span>
      <cite class="quote__author" style="top:116px">Lorem ipsum dolor</cite>
    </blockquote>
    <div class="base-band"></div>
  </section>

  <section class="panel panel--partners">
    <div class="photo photo--handshake" role="img" aria-label="Business handshake over a desk with keyboard and pen"></div>
    <div class="photo photo--inset photo--inset-c" role="img" aria-label="Health insurance form with a stethoscope"></div>
    <h2 class="section-title" style="left:20px;top:248px">Our partner:</h2>

    <div class="partner-group" style="left:23px;top:282px">
      <h3 class="partner-group__name">Labs</h3>
      <p class="partner-group__body">Lorem ipsum dolor sit amet, ligula suspendisse nulla pretium, rhoncus tempor fermentum</p>
    </div>
    <div class="partner-mark partner-mark--box" style="left:23px;top:355px">QUORVEN</div>
    <div class="partner-mark" style="left:180px;top:363px"><span class="partner-mark__dot"></span>Pelmora Bio</div>
    <div class="partner-mark" style="left:280px;top:363px">Halden Labs</div>

    <div class="partner-group" style="left:26px;top:408px">
      <h3 class="partner-group__name">Pharmacies</h3>
      <p class="partner-group__body">Lorem ipsum dolor sit amet, ligula suspendisse nulla pretium, rhoncus tempor fermentum</p>
    </div>
    <div class="partner-mark" style="left:23px;top:482px"><span class="partner-mark__square"></span>Brinvale Wellco</div>
    <div class="partner-mark" style="left:152px;top:482px">Tarqin Medix</div>
    <div class="partner-mark" style="left:266px;top:482px"><span class="partner-mark__square"></span>Ostrel Rx</div>

    <h2 class="section-title" style="left:23px;top:548px">References</h2>
    <div class="reference" style="top:592px">
      <div class="reference__photo ref--bottles" role="img" aria-label="Prescription bottles and pills"></div>
      <p class="reference__text">Lorem ipsum dolor sit amet, ligula suspendisse nulla pretium, rhoncus tempor fermentum, enim integer ad vestibulum volutpat. Nisl rhoncus turpis est, vel elit, congue wisi enim nunc ultricies sit, magna tincidunt.</p>
    </div>
    <div class="reference" style="top:709px">
      <div class="reference__photo ref--vial" role="img" aria-label="Clinician holding a medicine vial"></div>
      <p class="reference__text">Lorem ipsum dolor sit amet, ligula suspendisse nulla pretium, rhoncus tempor fermentum, enim integer ad vestibulum volutpat. Nisl rhoncus turpis est, vel elit, congue wisi enim nunc ultricies sit, magna tincidunt.</p>
    </div>
    <div class="base-band"></div>
  </section>

</main>
</body>
</html>
```